Stylish business cards for KV7

To create an appealing and professional business card design for a WOMEN Owned Construction Supply Company.
2 sided card. Incorporate brand elements, curvy, colorful, sleek and bright. No solid white background. attached samples of styles added shapes/ribbons. Want something with that WOW that looks awesome, factor. It is a new logo, so feel free to mess with logo colors in the blue and teal factors that can look good with both dark and light background. If you want to try a watermark with just the KV7, without the "Supply" that might look cool to.

Industry/Entity Type

Women owned construction supply company

Contact Information for Business Card

Name, Title, and phone number and email, web page. maybe spot for qr code.

Font styles to use
Sans Serif

Requirements
Nice to have
• would love to see colors, maybe stylish ribbon dividers or some sort of 2 or 3 tone color card that compliments logo.
Should not have
• Please do not have all white background. Do not include Home/reale state/ or building images.

```html
<!DOCTYPE html>
<html lang="en">
<head>
<meta charset="UTF-8">
<title>KV7 Supply – Business Cards</title>
<link rel="stylesheet" href="https://fonts.googleapis.com/css2?family=Poppins:wght@400;500;600;700&display=swap">
<style>
  :root {
    --stage: #2c2c2e;
    --card-dark: #0b0b0c;
    --card-light: #ffffff;
    --navy: #1f3b5c;
    --teal: #2196c1;
    --ink: #1d3557;
    --muted: #2a2a2a;
    --divider: #2f4d70;
  }
  * { box-sizing: border-box; margin: 0; padding: 0; }
  html, body { width: 1200px; height: 875px; overflow: hidden; }
  body {
    background: var(--stage);
    font-family: "Poppins", sans-serif;
    position: relative;
  }
  .card {
    position: absolute;
    width: 560px;
    height: 320px;
    border-radius: 22px;
    overflow: hidden;
    box-shadow: 0 18px 40px rgba(0,0,0,0.45);
  }
  .card--front {
    left: 80px;
    top: 90px;
    background: var(--card-dark);
    display: flex;
    align-items: center;
    justify-content: center;
  }
  .card--back {
    left: 560px;
    top: 470px;
    background: var(--card-light);
  }
  .wordmark {
    display: flex;
    align-items: center;
    gap: 12px;
    font-weight: 600;
    color: var(--teal);
    letter-spacing: 0.5px;
    white-space: nowrap;
  }
  .wordmark__dot {
    width: 14px;
    height: 14px;
    border-radius: 50%;
    background: var(--teal);
  }
  .card--front .wordmark { font-size: 52px; }
  .card--back .wordmark {
    position: absolute;
    left: 36px;
    top: 104px;
    font-size: 32px;
    color: var(--navy);
    z-index: 1;
  }
  .card--back .wordmark__dot { background: var(--navy); width: 10px; height: 10px; }
  .card__waves {
    position: absolute;
    inset: 0;
    width: 100%;
    height: 100%;
  }
  .card__divider {
    position: absolute;
    left: 286px;
    top: 50px;
    width: 1px;
    height: 130px;
    background: var(--divider);
    z-index: 1;
  }
  .contact {
    position: absolute;
    left: 306px;
    top: 38px;
    color: var(--muted);
    z-index: 1;
  }
  .contact__name {
    font-size: 19px;
    font-weight: 700;
    color: var(--ink);
    line-height: 1.1;
  }
  .contact__title {
    font-size: 11.5px;
    margin-bottom: 8px;
  }
  .contact__address {
    font-size: 11.5px;
    line-height: 1.35;
    margin-bottom: 8px;
  }
  .contact__list { list-style: none; font-size: 11.5px; line-height: 1.45; }
  .contact__list li { display: flex; align-items: center; gap: 7px; }
  .contact__icon { width: 10px; height: 10px; flex: none; fill: var(--teal); }
</style>
</head>
<body>

  <section class="card card--front" aria-label="Card front">
    <div class="wordmark"><span class="wordmark__dot"></span>KV7 Supply</div>
  </section>

  <section class="card card--back" aria-label="Card back">
    <svg class="card__waves" viewBox="0 0 560 320" preserveAspectRatio="none" aria-hidden="true">
      <path d="M0 320 L0 302 C70 250 170 246 300 242 C430 238 520 196 560 136 L560 320 Z" fill="var(--navy)"/>
      <path d="M310 234 C430 222 515 180 556 118" fill="none" stroke="#ffffff" stroke-width="9"/>
      <path d="M300 232 C425 216 512 172 554 104" fill="none" stroke="var(--teal)" stroke-width="5"/>
    </svg>

    <div class="wordmark"><span class="wordmark__dot"></span>KV7 Supply</div>
    <div class="card__divider"></div>

    <div class="contact">
      <p class="contact__name">DANIEL RIVERS</p>
      <p class="contact__title">General Manager</p>
      <p class="contact__address">48 Harbor Point Drive<br>Linden, NJ 07036 USA</p>
      <ul class="contact__list">
        <li><svg class="contact__icon" viewBox="0 0 10 10"><path d="M2 0 L4 2.5 L3 3.7 C3.6 5 5 6.4 6.3 7 L7.5 6 L10 8 L8.5 10 C4 9.5 0.5 6 0 1.5 Z"/></svg>+1.555.010.234</li>
        <li><svg class="contact__icon" viewBox="0 0 10 10"><path d="M0 2 H10 V8.5 H0 Z M0.6 2.4 L5 5.6 L9.4 2.4" fill="var(--teal)" stroke="#fff" stroke-width="0.8"/></svg>name@kv7supply.com</li>
        <li><svg class="contact__icon" viewBox="0 0 10 10"><circle cx="5" cy="5" r="4.5"/><path d="M0.5 5 H9.5 M5 0.5 C2.5 3 2.5 7 5 9.5 M5 0.5 C7.5 3 7.5 7 5 9.5" stroke="#fff" stroke-width="0.7" fill="none"/></svg>www.kv7supply.com</li>
      </ul>
    </div>
  </section>

</body>
</html>
```